Custom unique Stationary design for Logistics company

We need a custom, unique , elegant and luxurious full stationary design using our new logo, following these guidelines:
1- Business card: double sided, both sides uses the navy blue as the background main color (same as the code of the navy blue used in our logo).
2- envelope and folder: also use the same navy blue as the main background color.
3- book cover( notepad cover) : same thing with the navy blue
4- letterhead: feel free to use the combination of the colors in our logo.
5- rest of the items are up to your creativity

Target Market(s)

corporates and other businesses

Industry/Entity Type

Logistics and heavy machines contractors

Requirements
Must have
• Letterhead, business card, envelope, notepad cover, paper, file
Nice to have
• navy blue to be main background color for business card, envelope, notepad cover

```html
<!DOCTYPE html>
<html lang="en">
<head>
<meta charset="utf-8">
<title>Northbay Freight Stationery</title>
<link href="https://fonts.googleapis.com/css2?family=Open+Sans:wght@400;600;700&display=swap" rel="stylesheet">
<style>
  :root{
    --navy:#124c74;
    --navy-deep:#0b4f78;
    --orange:#f15a29;
    --ink:#4a4a4a;
    --paper:#ffffff;
    --backdrop:#e6e7e9;
  }
  *{box-sizing:border-box;margin:0;padding:0}
  html,body{width:1200px;height:1200px;overflow:hidden}
  body{background:var(--backdrop);font-family:"Open Sans",sans-serif;color:var(--ink);position:relative}

  .letterhead{position:absolute;left:50px;top:200px;width:620px;height:797px;background:var(--paper);box-shadow:0 6px 18px rgba(0,0,0,.18)}
  .brand{position:absolute;font-weight:700;color:var(--navy);display:flex;align-items:center;gap:8px;white-space:nowrap}
  .brand-dot{display:inline-block;border-radius:50%;background:var(--orange)}
  .letterhead .brand{right:64px;top:40px;font-size:26px}
  .letterhead .brand-dot{width:14px;height:14px}
  .letter-body{position:absolute;left:58px;right:60px;top:144px;font-size:10px;line-height:1.75}
  .letter-body p{margin-bottom:18px;text-align:justify}
  .recipient{line-height:1.25}
  .closing{margin-top:36px}
  .signature{width:140px;height:22px;margin:6px 0 8px;background:linear-gradient(90deg,rgba(74,74,74,.18),rgba(74,74,74,.05))}
  .signer-name{font-size:12.5px;font-weight:600;color:#333}
  .signer-role{font-size:10px;margin-top:2px}

  .letter-footer{position:absolute;left:0;right:0;bottom:0;height:72px;background:var(--navy);border-top:4px solid var(--orange);padding:10px 0 0 58px;color:#fff;font-size:11.5px}
  .contact-row{display:flex;align-items:center;gap:10px;margin-bottom:6px}
  .contact{display:flex;align-items:center;gap:4px}
  .icon{width:22px;height:22px;flex:none}

  .envelope-front{position:absolute;left:700px;top:420px;width:500px;height:250px;background:var(--paper);box-shadow:0 5px 14px rgba(0,0,0,.18)}
  .envelope-front .brand{left:32px;top:36px;font-size:20px}
  .envelope-front .brand-dot{width:11px;height:11px}
  .envelope-band{position:absolute;left:0;right:0;bottom:0;height:38px;background:var(--navy);border-top:3px solid var(--orange);color:#fff;font-size:9.5px;padding:10px 0 0 30px}

  .envelope-back{position:absolute;left:702px;top:725px;width:496px;height:246px;box-shadow:0 5px 14px rgba(0,0,0,.2)}
</style>
</head>
<body>

<section class="letterhead">
  <div class="brand"><span class="brand-dot"></span>Northbay Freight</div>

  <div class="letter-body">
    <p>Issuing Date: May 5, 2018</p>
    <p class="recipient">Name Of Employee Mr. XYZABC<br>Address of Employee<br>Address Line 2 etc..</p>
    <p style="margin-top:28px">Dear Mr.XYZABC</p>
    <p>Lorem Ipsum has been the industry's standard dummy text ever since the 1500s, when an unknown printer took a galley of type and scrambled it to make a type specimen book. It has survived not only five centuries, but also the leap into electronic typesetting, remaining essentially unchanged. It was popularised in the 1960s with the release of Letraset sheets containing Lorem Ipsum passages, and more recently with desktop publishing software like Aldus PageMaker including versions of Lorem Ipsum.</p>
    <p>Lorem Ipsum is simply dummy text of the printing and typesetting industry. Lorem Ipsum has been the industry's standard dummy text ever since the 1500s, when an unknown printer took a galley of type and scrambled it to make a type specimen book.</p>
    <p>It has survived not only five centuries, but also the leap into electronic typesetting, remaining essentially unchanged. It was popularised in the 1960s with the release of Letraset sheets containing Lorem Ipsum passages.</p>
    <div class="closing">Yours Sincerely</div>
    <div class="signature" role="img" aria-label="Handwritten signature of Daniel Mercer"></div>
    <div class="signer-name">Daniel Mercer</div>
    <div class="signer-role">Managing Director</div>
  </div>

  <footer class="letter-footer">
    <div class="contact-row">
      <span class="contact">
        <svg class="icon" viewBox="0 0 22 22"><circle cx="11" cy="11" r="11" fill="#f15a29"/><path d="M7 8c0-1 1-2 2-2l1 2-1 1c1 2 2 3 4 4l1-1 2 1c0 1-1 2-2 2-4 0-7-3-7-7z" fill="#fff"/></svg>
        044-555 010 200
      </span>
      <span class="contact">
        <svg class="icon" viewBox="0 0 22 22"><circle cx="11" cy="11" r="11" fill="#f15a29"/><rect x="5.5" y="7" width="11" height="8" fill="none" stroke="#fff" stroke-width="1.3"/><path d="M5.5 7l5.5 4.5L16.5 7" fill="none" stroke="#fff" stroke-width="1.3"/></svg>
        info@northbayfreight.com
      </span>
      <span class="contact">
        <svg class="icon" viewBox="0 0 22 22"><circle cx="11" cy="11" r="11" fill="#f15a29"/><circle cx="11" cy="11" r="5.5" fill="none" stroke="#fff" stroke-width="1.3"/><path d="M5.5 11h11M11 5.5c-2.5 3-2.5 8 0 11M11 5.5c2.5 3 2.5 8 0 11" fill="none" stroke="#fff" stroke-width="1"/></svg>
        www.northbayfreight.com
      </span>
    </div>
    <div class="contact-row">
      <span class="contact">
        <svg class="icon" viewBox="0 0 22 22"><circle cx="11" cy="11" r="11" fill="#f15a29"/><path d="M11 4.5a4.5 4.5 0 0 0-4.5 4.5c0 3.5 4.5 8.5 4.5 8.5s4.5-5 4.5-8.5A4.5 4.5 0 0 0 11 4.5z" fill="#fff"/><circle cx="11" cy="9" r="1.6" fill="#f15a29"/></svg>
        421, Address line goes here Country Name, 45452
      </span>
    </div>
  </footer>
</section>

<section class="envelope-front">
  <div class="brand"><span class="brand-dot"></span>Northbay Freight</div>
  <div class="envelope-band">421, Address line goes here Country Name, 45452</div>
</section>

<svg class="envelope-back" viewBox="0 0 496 246" aria-hidden="true">
  <rect width="496" height="246" fill="#0b4f78"/>
  <path d="M0 0 L18 55 L248 122 L478 55 L496 0" fill="#0d537d" stroke="#084466" stroke-width="2"/>
</svg>

</body>
</html>
```